Dunmore Roofing

Want a professional looking business card

Industry/Entity Type

Business

Contact Information for Business Card

Paul Dunmore ( Owner) paul@dunmoreroofing-example.com, www.dunmoreroofing-example.com, Adress: 4172 Township road 43 Maplebrook,ON K9X4T2

```html
<!DOCTYPE html>
<html lang="en">
<head>
<meta charset="utf-8">
<title>Dunmore Roofing – Business Card</title>
<link href="https://fonts.googleapis.com/css2?family=Open+Sans:wght@400;600;700&display=swap" rel="stylesheet">
<style>
  :root {
    --brand-blue: #1b4585;
    --card-white: #f5f3f2;
    --card-edge: #e6e2e0;
    --page-bg: #dcd8d6;
    --text-on-blue: #ffffff;
    --panel-rim: #8a8f99;
  }
  html, body {
    margin: 0;
    padding: 0;
    width: 1200px;
    height: 900px;
    overflow: hidden;
    background: var(--page-bg);
    font-family: "Open Sans", Arial, sans-serif;
  }
  .business-card {
    position: absolute;
    left: 120px;
    top: 157px;
    width: 960px;
    height: 585px;
    background: linear-gradient(135deg, #ffffff 0%, var(--card-white) 55%, var(--card-edge) 100%);
    box-shadow: 0 12px 30px rgba(0,0,0,0.18);
    overflow: hidden;
  }
  .brand-panel {
    position: absolute;
    left: 0;
    top: 0;
    width: 960px;
    height: 585px;
  }
  .contact-block {
    position: absolute;
    left: 44px;
    top: 88px;
    color: var(--text-on-blue);
  }
  .contact-name {
    margin: 0;
    font-size: 30px;
    font-weight: 600;
    line-height: 40px;
  }
  .contact-role {
    margin: 0;
    font-size: 23px;
    font-weight: 400;
    line-height: 32px;
  }
  .contact-address {
    margin: 24px 0 0;
    font-size: 23px;
    line-height: 34px;
    font-style: normal;
  }
  .contact-links {
    margin: 28px 0 0;
    padding: 0;
    list-style: none;
    font-size: 22px;
    line-height: 34px;
  }
  .contact-links li {
    display: flex;
    align-items: center;
    gap: 10px;
  }
  .contact-links svg {
    width: 18px;
    height: 18px;
    flex: none;
  }
  .company-name {
    position: absolute;
    left: 436px;
    top: 462px;
    width: 500px;
    text-align: center;
    margin: 0;
    font-size: 38px;
    font-weight: 700;
    letter-spacing: 2px;
    color: var(--brand-blue);
    text-transform: uppercase;
    white-space: nowrap;
    line-height: 1;
  }
</style>
</head>
<body>
  <div class="business-card">
    <svg class="brand-panel" viewBox="0 0 960 585" aria-hidden="true">
      <path d="M0 0 H268 C420 0 520 90 505 230 C495 330 420 390 325 410 L488 585 H0 Z" fill="var(--brand-blue)" stroke="var(--panel-rim)" stroke-width="3"/>
    </svg>

    <div class="contact-block">
      <h1 class="contact-name">PAUL DUNMORE</h1>
      <p class="contact-role">Owner</p>
      <address class="contact-address">4172 Township road 43<br>Maplebrook,ON K9X4T2</address>
      <ul class="contact-links">
        <li>
          <svg viewBox="0 0 20 20"><rect x="1" y="4" width="18" height="12" fill="#fff"/><path d="M1 4 L10 11 L19 4" fill="none" stroke="var(--brand-blue)" stroke-width="1.6"/></svg>
          paul@dunmoreroofing-example.com
        </li>
        <li>
          <svg viewBox="0 0 20 20"><circle cx="10" cy="10" r="9" fill="#fff"/><ellipse cx="10" cy="10" rx="4" ry="9" fill="none" stroke="var(--brand-blue)" stroke-width="1.4"/><line x1="1" y1="10" x2="19" y2="10" stroke="var(--brand-blue)" stroke-width="1.4"/></svg>
          www.dunmoreroofing-example.com
        </li>
      </ul>
    </div>

    <p class="company-name">Dunmore Roofing</p>
  </div>
</body>
</html>
```